Website redesign for a Medical Office

We are a physician office in need of a website redesign and a face-lift.
1.Website must work on all platforms including mobile phones and tablets.
2.Website will also include and interactive CONTACT US form and payment gateway for office to collect payment from patients online.
3.Website should have the ability for us to easily edit content without resorting to the services of an IT person.
4. Website content will be collected from the present website www.sunbrookkids.com.
- The type of upgrade we are looking for is more of a corrective work. The major problems with the current website are:
1. Contact Us form not working correctly
2. Credit card/monetrix gateway not working as intended
3. Needing better images/pictures to correctly reflect our business.
4. General enhancement to the overall feel and outlook of the current website.

5. Once a design is selected, website MUST be up and live within TWO WEEKS. The designer able to make this work within the time-frame will get an extra bonus.

Target Market(s)

General public; including patients and their parents.

Industry/Entity Type

Healthcare

Coding

Coded - Design and coding required

Number of Pages Required

5+ page

Font styles to use
Sans Serif

Colors
0492cd
33a6d7
85cae6
cee9f5
cedeed
acd036
cadf82
00a990
f04a50

Requirements
Must have
• 1. Ability for the website to work on all platforms including mobile phones and tablets.
• 2. Include an interactive CONTACT US form
• 3. A payment gateway for office to collect payment from patients online using credit cards and Monetrix.
• 4. Website should have the ability for us to easily edit content without resorting to the services of an IT person.
• 5. Once a design is selected, website MUST be up and live within TWO WEEKS.
• 6. Social network buttons.
• 7. A Vorlund map with office location or geo-tag and directions to office.
Nice to have
• Nice theme, children friendly with a flashy home page and inside pages.
• Attractive design with wow factor

```html
<!DOCTYPE html>
<html lang="en">
<head>
<meta charset="utf-8">
<title>Sunbrook Pediatrics</title>
<link rel="stylesheet" href="https://fonts.googleapis.com/css2?family=Open+Sans:wght@400;600;700&display=swap">
<style>
:root{
  --blue:#0492cd;
  --blue-mid:#33a6d7;
  --blue-light:#85cae6;
  --blue-pale:#cee9f5;
  --green:#acd036;
  --green-light:#cadf82;
  --teal:#00a990;
  --red:#f04a50;
  --ink:#3a3a3a;
  --muted:#666;
  --grey-btn:#dcdcdc;
  --footer:#333333;
  --footer-base:#2a2a2a;
}
*{box-sizing:border-box;margin:0;padding:0}
html,body{width:1200px;height:2601px;overflow:hidden}
body{font-family:"Open Sans",Arial,sans-serif;color:var(--ink);background:#fff;position:relative}
.abs{position:absolute}

.top-bar{left:0;top:0;width:1200px;height:61px;background:#f2f2f2}
.stripe{position:absolute;left:0;width:1200px;height:4px;display:flex}
.stripe span{flex:1}
.stripe .s1{background:var(--red)}.stripe .s2{background:var(--teal)}.stripe .s3{background:var(--blue)}.stripe .s4{background:var(--green)}
.social{left:60px;top:22px;display:flex;gap:14px;font-size:12px;font-weight:600;color:#555}
.hours{right:72px;top:22px;font-size:14px;font-weight:600;color:#555;display:flex;gap:10px;align-items:center}
.hours b{color:var(--blue)}

.nav-bar{left:0;top:61px;width:1200px;height:78px;background:#fff}
.brand{left:60px;top:14px;display:flex;align-items:center;gap:8px}
.brand-square{width:48px;height:48px;background:var(--blue);border-radius:4px}
.brand-name{font-size:19px;font-weight:700;color:var(--blue);line-height:1.05;letter-spacing:.5px}
.menu{left:348px;top:32px;display:flex;gap:40px;font-size:12px;font-weight:600;color:#333;text-transform:uppercase}
.menu .active{color:var(--red)}

.hero{left:0;top:139px;width:1200px;height:523px;background:linear-gradient(90deg,#f3f6f8 0%,#eef2f5 40%,#e4ebf0 70%,#dbe6ee 100%)}
.hero-title{left:73px;top:268px;font-size:45px;line-height:50px;font-weight:600;color:var(--blue-mid)}
.hero-title span{display:block;color:var(--red);font-weight:700}
.hero-text{left:73px;top:376px;width:500px;font-size:18px;line-height:26px;font-weight:600;color:#333}
.btn-green{left:73px;top:477px;width:182px;height:47px;background:var(--green);color:#fff;font-size:14px;font-weight:700;display:flex;align-items:center;justify-content:center}
.dots{left:75px;top:597px;display:flex;gap:6px}
.dots i{width:12px;height:12px;border-radius:50%;background:#555}
.dots i:first-child{background:var(--blue)}

.section-title{width:1200px;left:0;text-align:center;font-size:28px;font-weight:700;color:var(--blue)}
.lead{left:90px;width:1020px;text-align:center;font-size:15.5px;line-height:27px;color:#444}
.btn-grey{height:48px;background:var(--grey-btn);color:#333;font-size:14px;font-weight:600;display:flex;align-items:center;justify-content:center}

.services{left:75px;top:983px;width:1050px;height:514px;display:grid;grid-template-columns:1fr 1fr;grid-template-rows:1fr 1fr}
.service{padding:42px 44px 0 30px;color:#fff}
.service.general{background:var(--blue)}
.service.newborn{background:var(--red)}
.service.physical{background:var(--green)}
.service.emergency{background:var(--teal)}
.service-head{display:flex;align-items:center;gap:24px;font-size:25px;font-weight:600;margin-bottom:22px}
.service-head svg{width:60px;height:56px;flex:none}
.service p{font-size:14.5px;line-height:24px}

.archives{left:0;top:1548px;width:1200px;height:677px;background:var(--blue-pale)}
.card{top:1729px;width:330px;height:449px;background:#fff}
.card-image{width:330px;height:208px}
.card-body{padding:22px 18px 0}
.card h3{font-size:19px;font-weight:700;color:var(--red);margin-bottom:6px}
.card .meta{font-size:12.5px;color:var(--blue);margin-bottom:12px}
.card p{font-size:13.5px;line-height:24px;color:#444;margin-bottom:24px}
.card .btn-grey{width:180px}

.footer{left:0;top:2225px;width:1200px;height:293px;background:var(--footer);color:#ccc}
.footer h4{font-size:17px;font-weight:600;color:var(--green);margin-bottom:14px}
.footer-about{left:61px;top:46px;width:240px}
.footer-about p{font-size:13px;line-height:23px}
.links{left:394px;top:50px}
.links li{list-style:none;font-size:13px;line-height:34px}
.contact{left:624px;top:50px;font-size:13px;line-height:23px}
.contact b{color:#fff}
.contact .row{display:flex;gap:16px;align-items:center;margin-top:8px}
.map{left:870px;top:46px;width:271px;height:182px;background:linear-gradient(135deg,#e9e6df,#f3f1ec 50%,#dfe6d8)}
.base{left:0;top:2523px;width:1200px;height:78px;background:var(--footer-base)}
.copy{left:75px;top:31px;font-size:12px;color:#aaa}
.pay{right:60px;top:26px;display:flex;gap:10px}
.pay span{background:#d6d6d6;color:#333;font-size:10px;font-weight:700;padding:6px 7px;border-radius:2px}
</style>
</head>
<body>

<header class="abs top-bar">
  <div class="stripe" style="top:0"><span class="s1"></span><span class="s2"></span><span class="s3"></span><span class="s4"></span></div>
  <div class="abs social"><span>Friendly</span><span>Chirpr</span><span>Linkly</span><span>Vorlund+</span><span>Pixgram</span></div>
  <div class="abs hours">
    <span>Opening Hours : <b>M-F 8:30AM - 5:30PM</b></span>
    <svg width="14" height="14" viewBox="0 0 16 16"><path fill="#555" d="M3 1h3l1.5 4-2 1.2a9 9 0 0 0 4.3 4.3L11 8.5l4 1.5v3c0 1-1 2-2 2A12 12 0 0 1 1 3c0-1 1-2 2-2z"/></svg>
    <span>Contact : <b>(555) 014-2280</b></span>
  </div>
</header>

<nav class="abs nav-bar">
  <div class="abs brand"><div class="brand-square"></div><div class="brand-name">SUNBROOK<br>PEDIATRICS</div></div>
  <ul class="abs menu" style="list-style:none">
    <li class="active">Home</li><li>About Us</li><li>Our Services</li><li>Sunbrook Health Center</li><li>Forms</li><li>Latest News</li><li>Contact Us</li>
  </ul>
</nav>

<section class="abs hero" role="img" aria-label="Photo of a smiling pediatrician holding a baby while using a stethoscope"></section>
<h1 class="abs hero-title">Medical Services<span>That You Can Trust</span></h1>
<p class="abs hero-text">Sunbrook Pediatrics exists to serve the children and families of Harlan Co. and the surrounding areas with the most efficient and best quality healthcare.</p>
<div class="abs btn-green">READ MORE</div>
<div class="abs dots"><i></i><i></i><i></i><i></i></div>

<h2 class="abs section-title" style="top:715px">WELCOME TO SUNBROOK PEDIATRICS!</h2>
<p class="abs lead" style="top:770px">Sunbrook Pediatrics is a modern pediatric practice dedicated to the health and wellness of children. It is the pediatrician office of choice in Millbrook, Georgia. At Sunbrook Pediatrics, you will find a pediatrician and an environment that is warm and compassionate.<br>All of our staff members are knowledgeable, caring, efficient, and ready to serve you.</p>
<div class="abs btn-grey" style="left:510px;top:883px;width:180px">READ MORE</div>

<section class="abs services">
  <div class="service general">
    <div class="service-head"><svg viewBox="0 0 24 22"><path fill="#fff" d="M12 21 2.5 11.5A5.5 5.5 0 0 1 12 4a5.5 5.5 0 0 1 9.5 7.5z"/></svg>General Medical Care</div>
    <p>Routine Office visits for common ailment, Immunizations, ADHD Evaluation and Treatment, Asthma Care, Allergy Testing, Same day SICK appointments..</p>
  </div>
  <div class="service newborn">
    <div class="service-head"><svg viewBox="0 0 24 24"><circle cx="12" cy="4" r="3" fill="#fff"/><path fill="#fff" d="M4 8h16v3h-5v12h-2.5v-6h-1v6H9V11H4z"/></svg>Newborn Care</div>
    <p>Evaluation of the newborn, Infant circumcision.</p>
  </div>
  <div class="service physical">
    <div class="service-head"><svg viewBox="0 0 24 24"><circle cx="12" cy="6" r="4.5" fill="none" stroke="#fff" stroke-width="2"/><path fill="none" stroke="#fff" stroke-width="2" d="M3 23v-4a6 6 0 0 1 6-6h6a6 6 0 0 1 6 6v4z"/><path fill="none" stroke="#fff" stroke-width="1.6" d="M9 13v5m6-5v4"/></svg>Physical Examinations</div>
    <p>Routine Annual Physicals, Sports Physicals, School and College Physicals, Camp Physicals.</p>
  </div>
  <div class="service emergency">
    <div class="service-head"><svg viewBox="0 0 24 22"><rect x="1" y="5" width="22" height="16" rx="2" fill="none" stroke="#fff" stroke-width="2"/><path fill="none" stroke="#fff" stroke-width="2" d="M8 5V2h8v3"/><path fill="#fff" d="M10.5 8.5h3v3h3v3h-3v3h-3v-3h-3v-3h3z"/></svg>Emergency Care</div>
    <p>Management of simple injuries, Strains and sprains, Lacerations, Drainage of simple cysts and abscesses, Removal of foreign bodies and splints.</p>
  </div>
</section>

<section class="abs archives"></section>
<h2 class="abs section-title" style="top:1588px">FROM OUR MEDICAL ARCHIVES</h2>
<p class="abs lead" style="top:1641px;font-size:15px;color:#555">There is nothing more joyful to us as loving parents than that moment when we hold our precious little baby, or babies, in our arms after birth.<br>We should acknowledge them as gifts from God and count ourselves blessed to have them.</p>

<article class="abs card" style="left:75px">
  <div class="card-image" role="img" aria-label="Photo of a sick child resting in bed while medicine is poured" style="background:linear-gradient(135deg,#f1e6dc,#e8d2c2 60%,#c9b6a8)"></div>
  <div class="card-body"><h3>Common Childhood Illnesses</h3><div class="meta">14 December, 2016, &nbsp; By Admin</div><p>As they grow and develop, children come in contact with and may sometimes suffer from a variety of common illnesses....</p><div class="btn-grey">READ MORE</div></div>
</article>
<article class="abs card" style="left:434px">
  <div class="card-image" role="img" aria-label="Photo of a pregnant woman relaxing on a white sofa" style="background:linear-gradient(135deg,#f6f6f6,#e6e8ee 55%,#8aa0c8)"></div>
  <div class="card-body"><h3>Now That You Are Pregnant</h3><div class="meta">14 December, 2016, &nbsp; By Admin</div><p>As they grow and develop, children come in contact with and may sometimes suffer from a variety of common illnesses....</p><div class="btn-grey">READ MORE</div></div>
</article>
<article class="abs card" style="left:793px">
  <div class="card-image" role="img" aria-label="Photo of a mother asleep beside her newborn baby" style="background:linear-gradient(135deg,#dfe8f2,#f2ece8 55%,#e6d4c8)"></div>
  <div class="card-body"><h3>Newborn Care</h3><div class="meta">14 December, 2016, &nbsp; By Admin</div><p>As they grow and develop, children come in contact with and may sometimes suffer from a variety of common illnesses....</p><div class="btn-grey">READ MORE</div></div>
</article>

<footer class="abs footer">
  <div class="abs footer-about">
    <div style="display:flex;align-items:center;gap:8px;margin-bottom:18px"><div class="brand-square"></div><div class="brand-name" style="color:#fff">SUNBROOK<br>PEDIATRICS</div></div>
    <p>At Sunbrook Pediatrics, you will find a pediatrician and an environment that is warm and compassionate. All of our staff members are knowledgeable, caring, efficient, and ready to serve you.</p>
  </div>
  <div class="abs links"><h4>Quick Links</h4><ul><li>Home</li><li>About Us</li><li>Services</li><li>Make an Appointment</li><li>Contact Us</li></ul></div>
  <div class="abs contact">
    <h4>Contact Info</h4>
    <b>Sunbrook Pediatrics</b><br>48 Alder Park Millbrook,<br>GA 30190
    <div class="row"><svg width="12" height="12" viewBox="0 0 16 16"><path fill="#ccc" d="M3 1h3l1.5 4-2 1.2a9 9 0 0 0 4.3 4.3L11 8.5l4 1.5v3c0 1-1 2-2 2A12 12 0 0 1 1 3c0-1 1-2 2-2z"/></svg>(555)-014-2280</div>
    <div class="row"><svg width="12" height="10" viewBox="0 0 16 12"><rect width="16" height="12" fill="#ccc"/><path d="M0 0l8 6 8-6" fill="none" stroke="#333" stroke-width="1.5"/></svg>info@sunbrookkids.com</div>
    <div class="row"><svg width="12" height="14" viewBox="0 0 12 16"><path fill="#ccc" d="M6 0a6 6 0 0 1 6 6c0 4-6 10-6 10S0 10 0 6a6 6 0 0 1 6-6z"/><circle cx="6" cy="6" r="2" fill="#333"/></svg>Map Location</div>
  </div>
  <div class="abs map" role="img" aria-label="Vorlund map showing the office location"></div>
</footer>
<div class="stripe" style="top:2518px"><span class="s1"></span><span class="s2"></span><span class="s3"></span><span class="s4"></span></div>
<div class="abs base">
  <div class="abs copy">© Copyright 2017. Sunbrook Pediatrics All Rights Reserved</div>
  <div class="abs pay"><span>Monetrix</span><span>Cardora</span><span>Findex</span><span>Vantapay</span><span>Amplex</span></div>
</div>

</body>
</html>
```